Laser Tattoo Removal Business Cards

We are looking for a professional business card design for a laser tattoo removal business. Ideally looking for a black business card design. The name of the business is Brightline Tattoo Removal. We place our cards at local tattoo shops so we ideally are looking for something trendy/edgy to draw both male and female clientele in.

Target Market(s)

Male/Female ages 18-60

Contact Information for Business Card

black background ideally.. hoping to stay within greys, whites and black

Font styles to use
Serif
Sans Serif

Colors
121212
a9a9a9
5c5c5c
f5f5f5
ffffff
7f7f7f
606060
848484
9d9d9d

Requirements
Must have
• Employee Info:
• Melissa Thornbury
• Chief Executive Offer
• m: 919.537.2846
• w: 919.362.4178
• f: 919.685.3907
• mthornbury@brightlinetattooremoval.example
• Address:
• 4615 Oakmere Pkwy, Suite 210
• Raleigh, NC 27654
• Website:
• www.brightlinetattooremoval.example
Nice to have
• Myabe business name on back or logo on back and employee info on the front

```html
<!DOCTYPE html>
<html lang="en">
<head>
<meta charset="utf-8">
<title>Brightline Tattoo Removal – Business Cards</title>
<link href="https://fonts.googleapis.com/css2?family=Roboto:wght@400;500&family=Roboto+Condensed:wght@500;700&display=swap" rel="stylesheet">
<style>
  :root {
    --ink: #121212;
    --panel-dark: #2a2a2a;
    --card-back: #1b1b1b;
    --paper: #f5f5f5;
    --white: #ffffff;
    --grey-strip: #9d9d9d;
    --grey-mid: #5c5c5c;
    --stage: #d9d9d9;
  }
  * { box-sizing: border-box; margin: 0; padding: 0; }
  html, body { width: 1200px; height: 960px; overflow: hidden; }
  body {
    position: relative;
    background: var(--stage);
    font-family: "Roboto", Arial, sans-serif;
  }
  .card {
    position: absolute;
    width: 600px;
    height: 344px;
    box-shadow: 0 3px 8px rgba(0,0,0,.35);
    overflow: hidden;
  }
  /* Front */
  .card-front { left: 313px; top: 113px; display: flex; }
  .brand-panel {
    position: relative;
    flex: none;
    width: 280px;
    background: var(--paper);
    border-left: 9px solid var(--grey-strip);
    display: flex;
    align-items: center;
    justify-content: center;
  }
  .brand-name {
    font-family: "Roboto Condensed", Arial, sans-serif;
    font-weight: 700;
    text-transform: uppercase;
    text-align: center;
    line-height: 1.1;
  }
  .brand-panel .brand-name {
    color: var(--ink);
    font-size: 30px;
    letter-spacing: 2px;
  }
  .brand-panel .brand-name small,
  .card-back .brand-name small {
    display: block;
    font-size: .52em;
    letter-spacing: 3px;
    margin-top: 10px;
  }
  .info-panel {
    flex: 1;
    min-width: 0;
    background: var(--panel-dark);
    color: var(--white);
    padding: 60px 20px 0 30px;
  }
  .person-name {
    font-family: "Roboto Condensed", Arial, sans-serif;
    font-weight: 700;
    font-size: 20px;
    text-transform: uppercase;
    line-height: 1.1;
  }
  .person-title {
    font-family: "Roboto", Arial, sans-serif;
    font-weight: 500;
    font-size: 14.5px;
    line-height: 1.2;
  }
  .address {
    margin-top: 46px;
    font-size: 14px;
    line-height: 18px;
    font-style: normal;
  }
  .contact-list {
    list-style: none;
    margin-top: 9px;
    font-size: 14px;
  }
  .contact-list li {
    display: flex;
    align-items: center;
    height: 19.2px;
    white-space: nowrap;
  }
  .contact-list .contact-email { font-size: 12px; letter-spacing: -0.1px; }
  .contact-list svg {
    width: 13px;
    height: 13px;
    margin-right: 10px;
    fill: var(--white);
    flex: none;
  }
  /* Back */
  .card-back {
    left: 311px;
    top: 472px;
    background: var(--card-back);
    color: var(--white);
  }
  .card-back .brand-name {
    position: absolute;
    left: 0; right: 0; top: 110px;
    font-size: 48px;
    letter-spacing: 4px;
    color: var(--white);
  }
  .card-back .brand-name small { font-size: 20px; letter-spacing: 4px; margin-top: 16px; }
  .back-website {
    position: absolute;
    left: 0; right: 0; top: 292px;
    text-align: center;
    font-size: 13px;
    letter-spacing: 3px;
  }
</style>
</head>
<body>

<section class="card card-front">
  <div class="brand-panel">
    <p class="brand-name">Brightline<small>Tattoo Removal</small></p>
  </div>
  <div class="info-panel">
    <h1 class="person-name">Melissa Thornbury</h1>
    <p class="person-title">Chief Executive Offer</p>
    <address class="address">4615 Oakmere Pkwy, Suite 210<br>Raleigh, NC 27654</address>
    <ul class="contact-list">
      <li><svg viewBox="0 0 16 16"><path d="M3.6 1l2.6 2.9-1.4 2c.9 2 2.5 3.6 4.5 4.5l2-1.4L14.2 11.7 12.8 14.5C7 14 2 9 1.5 3.2z"/></svg>919.362.4178</li>
      <li><svg viewBox="0 0 16 16"><path d="M4 0h8v16H4zM5.5 2v10h5V2zM7.2 13.2h1.6v1.4H7.2z" fill-rule="evenodd"/></svg>919.537.2846</li>
      <li><svg viewBox="0 0 16 16"><path d="M4 1h8v4H4zM1 6h14v7h-3v2H4v-2H1zM5 10v4h6v-4z" fill-rule="evenodd"/></svg>919.685.3907</li>
      <li class="contact-email"><svg viewBox="0 0 16 16"><path d="M1 3.5h14v9H1zM2 4.5l6 4.5 6-4.5"/></svg>mthornbury@brightlinetattooremoval.example</li>
      <li><svg viewBox="0 0 16 16"><circle cx="8" cy="8" r="7"/></svg>www.brightlinetattooremoval.example</li>
    </ul>
  </div>
</section>

<section class="card card-back">
  <p class="brand-name">Brightline<small>Tattoo Removal</small></p>
  <p class="back-website">www.brightlinetattooremoval.example</p>
</section>

</body>
</html>
```